Business Card Design Project

I require a business card with the following information on them for various different people;
name
m:
f:
e:
I have a logo already and will attached that. We are in the construction industry. I require something clean and simple but eye catching at the same time. You can use another colour with our logo if you like and you can style the logo as well if you wish. I am open.
Also it needs to be front and back design.
Industry/Entity Type
Construction
Requirements
Must have
- Logo, name, mobile, fax and email address.
Front and back design

```html
<!DOCTYPE html>
<html lang="en">
<head>
<meta charset="utf-8">
<title>Northfield Developments – Business Cards</title>
<link href="https://fonts.googleapis.com/css2?family=Open+Sans:wght@400;700&family=Questrial&display=swap" rel="stylesheet">
<style>
  :root {
    --stage: #ecebe7;
    --paper: #ffffff;
    --brand-green: #5db446;
    --brand-green-light: #b9da5a;
    --band-grey: #4d4d4d;
    --text-grey: #555555;
    --card-edge: #d4d2cc;
  }
  * { box-sizing: border-box; margin: 0; padding: 0; }
  html, body {
    width: 1200px;
    height: 757px;
    overflow: hidden;
    background: var(--stage);
  }
  .canvas {
    position: relative;
    width: 1200px;
    height: 757px;
  }
  .card {
    position: absolute;
    width: 512px;
    height: 292px;
    background: var(--paper);
    border: 1px solid var(--card-edge);
    overflow: hidden;
  }
  .card--front { left: 73px; top: 61px; }
  .card--back  { left: 621px; top: 61px; }
  .card--feature {
    left: 352px; top: 403px;
    border: none;
    background: radial-gradient(ellipse at 55% 40%, var(--brand-green-light) 0%, var(--brand-green) 62%);
  }

  .wordmark {
    display: flex;
    align-items: center;
    justify-content: center;
    gap: 10px;
    font-family: "Questrial", "Century Gothic", sans-serif;
    color: var(--brand-green);
    white-space: nowrap;
  }
  .wordmark__square {
    width: 22px; height: 22px;
    background: var(--brand-green);
    flex: none;
  }
  .card--front .wordmark {
    position: absolute; left: 0; right: 0; top: 58px;
    font-size: 30px;
  }
  .card--back .wordmark {
    position: absolute; left: 0; right: 0; top: 128px;
    font-size: 33px;
  }
  .card--back .wordmark__square { width: 26px; height: 26px; }
  .card--feature .wordmark {
    position: absolute; left: 0; right: 0; top: 124px;
    font-size: 38px;
    color: var(--paper);
  }

  .rule {
    position: absolute; left: 0; right: 0;
    height: 2px;
    background: linear-gradient(90deg, var(--brand-green), var(--brand-green-light) 50%, var(--brand-green));
  }
  .rule--top { top: 143px; }
  .rule--bottom { top: 236px; }

  .contact-band {
    position: absolute; left: 0; right: 0; top: 147px;
    height: 86px;
    background: var(--band-grey);
    color: var(--paper);
    font-family: "Open Sans", Arial, sans-serif;
    font-size: 12.5px;
    text-align: center;
    padding-top: 24px;
  }
  .contact-band__row {
    display: flex;
    justify-content: center;
    align-items: center;
    gap: 10px;
    line-height: 26px;
  }
  .contact-item {
    display: inline-flex;
    align-items: center;
    gap: 5px;
  }
  .contact-item svg { fill: var(--paper); }

  .holder {
    position: absolute; left: 0; right: 0; top: 260px;
    text-align: center;
    font-family: "Open Sans", Arial, sans-serif;
    color: var(--text-grey);
    font-size: 15px;
  }
  .holder__name { font-weight: 700; }
  .holder__title { font-size: 14px; }
</style>
</head>
<body>
<main class="canvas">

  <section class="card card--front" aria-label="Business card front">
    <div class="wordmark">
      <span class="wordmark__square"></span>
      <span class="wordmark__name">Northfield Developments</span>
    </div>
    <div class="rule rule--top"></div>
    <div class="contact-band">
      <div class="contact-band__row">
        <span class="contact-item">
          <svg width="7" height="11" viewBox="0 0 7 11" aria-label="Mobile"><rect x="0" y="0" width="7" height="11" rx="1.2"/><rect x="1.2" y="1.5" width="4.6" height="5" fill="#4d4d4d"/></svg>
          +91 98765 43210
        </span>
        <span class="contact-item">
          <svg width="11" height="10" viewBox="0 0 11 10" aria-label="Fax"><rect x="2.5" y="0" width="6" height="3.5"/><rect x="0" y="3" width="11" height="5" rx="1"/><rect x="2.5" y="7" width="6" height="3"/></svg>
          +91 98765 43211
        </span>
      </div>
      <div class="contact-band__row">
        <span class="contact-item">
          <svg width="10" height="7" viewBox="0 0 10 7" aria-label="Email"><rect width="10" height="7"/><path d="M0 0 L5 4 L10 0" fill="none" stroke="#4d4d4d" stroke-width="1"/></svg>
          hello@northfieldbuild.com
        </span>
      </div>
    </div>
    <div class="rule rule--bottom"></div>
    <p class="holder"><span class="holder__name">Your Name ,</span> <span class="holder__title">Title</span></p>
  </section>

  <section class="card card--back" aria-label="Business card back">
    <div class="wordmark">
      <span class="wordmark__square"></span>
      <span class="wordmark__name">Northfield Developments</span>
    </div>
  </section>

  <section class="card card--feature" aria-label="Business card green reverse">
    <div class="wordmark">
      <span class="wordmark__name">Northfield</span>
    </div>
  </section>

</main>
</body>
</html>
```